Birch And Harbor Website A Website design for book editing

A website design for book editing

Our proofreading, editing and manuscript review packages are specifically tailored to help you publish the best possible version of your story.

NEED HELP PUBLISHING A BESTSELLER?

If you’re looking for professional book editing services from senior publishing industry insiders, look no further. Besides editing, we can also answer all your publishing questions and get you started building your author platform.

OUR SERVICES

We've carefully structured our packages to maximize value for every budget.

PRICING

$.02
PER WORD
Proofreading
Line Edit (Copy-editing)
Fix spelling and grammar
Sales copy/summary revision

$.04
PER WORD
Proofreading
Line Edit (Copy-editing)
Fix spelling and grammar
Organization and content
Plot and pacing
Manuscript Review

$.06
PER WORD
Proofreading
Line Edit (Copy-editing)
Fix spelling and grammar
Organization and content
Plot and pacing
Manuscript Review
Formatting (print and ebook)
Pre-publication proofread

OUR PROCESS

Send us a sample of your book. Our caffeine-fueled, eagle-eyed editors will go through it and then email you with their comments and suggestions. You can ask them any questions you want. They will look for…

Typos and grammatical errors.
Spelling and word choice issues
Punctuation and style
Word choice, clarity and flow.
Sentence structure and craft
If your writing is already clean, then they’ll discuss bigger picture things with you, like theme, concept, purpose, audience, potential market and branding (including title, subtitle, and tagline or elevator pitch).

Once you feel comfortable and confident in an editor’s expertise, skill and knowledge, and are ready to move ahead, we’ll send an invoice for the first half of the total word count so the editor can get started. We’ll charge the rest when the project is close to completion.

Target Market(s)

Authors

Industry/Entity Type

Book Publisher

Coding

Coded - Design and coding required

Number of Pages Required

1 page

Requirements
Must have
• OUR SERVICES
• We've carefully structured our packages to maximize value for every budget.
• PRICING
• $.02
• PER WORD
• Proofreading
• Line Edit (Copy-editing)
• Fix spelling and grammar
• Sales copy/summary revision
• $.04
• PER WORD
• Proofreading
• Organization and content
• Plot and pacing
• Manuscript Review
• $.06
• PER WORD
• Proofreading
• Plot and pacing
• Manuscript Review
• Formatting (print and ebook)
• Pre-publication proofread

```html
<!DOCTYPE html>
<html lang="en">
<head>
<meta charset="utf-8">
<title>Birch And Harbor — Book Editing</title>
<link href="https://fonts.googleapis.com/css2?family=Roboto:ital,wght@0,400;0,500;0,700;0,900;1,400;1,700&display=swap" rel="stylesheet">
<style>
:root{
  --red:#e1001a;
  --red-dark:#b80016;
  --ink:#1d1d1d;
  --text:#555;
  --grey-head:#474747;
  --grey-bg:#f3f3f3;
  --dark:#2b2b2b;
  --black:#050505;
  --white:#fff;
}
*{box-sizing:border-box;margin:0;padding:0}
html,body{width:1200px;height:3422px;overflow:hidden}
body{font-family:'Roboto',Arial,sans-serif;color:var(--ink);background:var(--white);position:relative}
a{color:inherit;text-decoration:none}
ul{list-style:none}

/* Header */
.site-header{height:125px;position:relative}
.brand{position:absolute;left:103px;top:34px;font-size:42px;font-weight:700;color:var(--red);letter-spacing:-.5px}
.header-contact{position:absolute;right:82px;top:26px;display:flex;align-items:center;gap:10px;font-size:16px;color:#333}
.header-contact .phone{display:flex;align-items:center;gap:10px;margin-right:20px}
.social-dot{width:30px;height:30px;border-radius:50%;display:inline-block}
.dot-a{background:#3b5a9a}.dot-b{background:#1f7bc1}
.main-nav{position:absolute;top:84px;left:0;right:0}
.main-nav a{position:absolute;font-size:12.5px;font-weight:700;color:#111;transform:translateX(-50%);letter-spacing:.2px}
.main-nav a.active{color:var(--red)}

/* Hero */
.hero{height:578px;position:relative;color:var(--white);text-align:center;overflow:hidden}
.hero-photo{position:absolute;inset:0;background:linear-gradient(120deg,#556273 0%,#3a4656 45%,#26303c 100%)}
.hero-shade{position:absolute;inset:0;background:rgba(10,15,25,.35)}
.hero h1{position:absolute;top:264px;left:0;right:0;font-size:44px;font-weight:700;letter-spacing:.3px}
.hero p{position:absolute;top:325px;left:250px;right:250px;font-size:18.5px;line-height:28px}
.btn-pill{display:inline-block;border-radius:20px;font-weight:700;font-size:13px;text-align:center}
.hero .btn-pill{position:absolute;top:422px;left:538px;width:125px;height:37px;line-height:37px;background:var(--white);color:var(--red)}

/* About */
.about{height:376px;position:relative;overflow:hidden}
.about-photo{position:absolute;left:0;top:0;width:720px;height:100%;background:linear-gradient(135deg,#8a8f96 0%,#c9c3b6 45%,#6f7479 100%)}
.about-panel{position:absolute;inset:0}
.about-body{position:absolute;left:718px;top:50px;width:380px;color:var(--white)}
.about-body h2{font-size:25px;font-weight:700;color:var(--black);margin-bottom:16px}
.about-body h2 span{color:var(--white)}
.about-body p{font-size:12.5px;line-height:23.5px}
.about-body .btn-pill{margin-top:20px;width:125px;height:37px;line-height:37px;background:var(--white);color:var(--red)}

/* Section titles */
.section-title{text-align:center;font-size:25px;font-weight:700;color:var(--black)}
.section-title span{color:var(--red)}

/* Services */
.services{height:563px;position:relative}
.services .section-title{position:absolute;top:86px;left:0;right:0}
.services .lead{position:absolute;top:130px;left:0;right:0;text-align:center;font-size:14.5px;color:var(--text)}
.service{position:absolute;top:194px;width:300px;transform:translateX(-50%);text-align:center}
.service .icon{width:137px;height:137px;margin:0 auto;display:block}
.service h3{margin-top:26px;font-size:16px;font-weight:500}
.service p{margin-top:12px;font-size:12.5px;line-height:25px;color:#444}
.services .btn-pill{position:absolute;top:465px;left:509px;width:182px;height:46px;line-height:46px;background:var(--red);color:var(--white);font-size:12.5px}

/* Packages */
.packages{height:605px;background:var(--grey-bg);position:relative}
.packages .section-title{position:absolute;top:52px;left:0;right:0}
.plan{position:absolute;background:var(--white);box-shadow:0 2px 10px rgba(0,0,0,.12);text-align:center}
.plan-silver{left:228px;top:149px;width:240px;height:365px}
.plan-gold{left:465px;top:130px;width:265px;height:411px;z-index:2}
.plan-platinum{left:730px;top:149px;width:244px;height:371px}
.plan-head{position:relative;height:88px}
.plan-gold .plan-head{height:105px}
.plan-head svg{position:absolute;inset:0;width:100%;height:100%}
.plan-head h3{position:relative;padding-top:28px;font-size:17px;font-weight:700;color:var(--white)}
.plan-price{margin-top:12px;font-size:22px;font-weight:700;color:#333}
.plan-gold .plan-price{color:var(--red)}
.plan-unit{font-size:13.5px;color:#555;margin-top:2px}
.plan ul{text-align:left;margin:14px 0 0 34px}
.plan li{display:flex;align-items:center;gap:12px;font-size:12px;color:#444;height:26px}
.plan li svg{flex:none}
.plan-note{font-size:12px;color:#444;line-height:20px;margin-top:16px}
.plan .btn-pill{margin-top:12px;width:100px;height:26px;line-height:26px;font-size:10.5px;color:var(--white);background:#3d3d3d}
.plan-gold .btn-pill{background:var(--red);width:110px}

/* Process */
.process{height:372px;position:relative}
.process .section-title{position:absolute;top:46px;left:0;right:0}
.process-steps{position:absolute;top:130px;left:0;width:1200px;height:200px}
.step{position:absolute;top:0;width:200px;transform:translateX(-50%);text-align:center}
.step svg{display:block;margin:0 auto}
.step p{margin-top:20px;font-size:13px;color:#444}
.connector{position:absolute;top:52px}

/* Testimonials */
.testimonials{height:399px;position:relative;overflow:hidden;color:var(--white)}
.testimonials-photo{position:absolute;inset:0;background:radial-gradient(circle at 55% 60%,#5d5d5d 0%,#3a3a3a 45%,#262626 100%)}
.testimonials .section-title{position:absolute;top:38px;left:0;right:0;color:var(--red);font-weight:500;font-size:27px}
.quote{position:absolute;top:114px;width:420px;transform:translateX(-50%);text-align:center}
.quote blockquote{font-size:12px;font-weight:700;font-style:italic;line-height:23px}
.avatar{width:68px;height:68px;border-radius:50%;background:linear-gradient(#d9cfc4,#9c8f82);border:3px solid var(--white);margin:24px auto 0}
.quote .name{margin-top:20px;font-size:12.5px;font-weight:700}
.quote .city{margin-top:10px;font-size:11px;font-weight:700;font-style:italic}

/* Footer */
.site-footer{height:404px;background:var(--black);color:var(--white);position:relative}
.footer-col{position:absolute;top:62px}
.footer-brand{left:100px;width:240px}
.footer-brand .name{font-size:27px;font-weight:700;line-height:80px;height:80px}
.footer-brand p{margin-top:18px;font-size:12.5px;line-height:23px}
.footer-social{display:flex;gap:14px;margin-top:22px}
.footer-social span{width:37px;height:37px;border-radius:50%;background:var(--red)}
.footer-col h4{font-size:18px;font-weight:500;margin-bottom:18px;margin-top:4px}
.newsletter{left:376px;width:300px}
.newsletter p{font-size:12.5px;line-height:23px}
.newsletter .field{margin-top:18px;width:287px;height:34px;background:var(--white);color:#888;font-size:12px;line-height:34px;padding-left:14px}
.newsletter .btn-sub{margin-top:19px;width:132px;height:34px;line-height:34px;background:var(--red);font-size:12.5px;font-weight:700;text-align:center}
.contact{left:718px;width:240px}
.contact li{display:flex;gap:14px;font-size:12.5px;line-height:22px;margin-bottom:12px}
.contact li svg{flex:none;margin-top:4px}
.quick-links{left:985px}
.quick-links li{font-size:12px;line-height:22px}
.quick-links li::before{content:"\00BB";margin-right:8px}
.footer-rule{position:absolute;left:100px;right:100px;top:317px;border-top:1px solid #222}
.copyright{position:absolute;top:350px;left:0;right:0;text-align:center;font-size:12px}
</style>
</head>
<body>

<header class="site-header">
  <div class="brand">Birch And Harbor</div>
  <div class="header-contact">
    <span class="phone">
      <svg width="16" height="16" viewBox="0 0 24 24"><path fill="#e1001a" d="M6.6 10.8a15.1 15.1 0 0 0 6.6 6.6l2.2-2.2a1 1 0 0 1 1-.25 11.4 11.4 0 0 0 3.6.6 1 1 0 0 1 1 1V20a1 1 0 0 1-1 1A17 17 0 0 1 3 4a1 1 0 0 1 1-1h3.5a1 1 0 0 1 1 1c0 1.25.2 2.45.6 3.6a1 1 0 0 1-.25 1z"/></svg>
      02 5550 0142
    </span>
    <span class="social-dot dot-a"></span>
    <span class="social-dot dot-b"></span>
  </div>
  <nav class="main-nav">
    <a class="active" style="left:506px">HOME</a>
    <a style="left:609px">SERVICES</a>
    <a style="left:725px">ABOUT US</a>
    <a style="left:839px">PROCESS</a>
    <a style="left:949px">PRICING</a>
    <a style="left:1067px">CONTACT US</a>
  </nav>
</header>

<section class="hero">
  <div class="hero-photo" role="img" aria-label="Photo of hands reviewing and signing manuscript pages beside a cup of coffee"></div>
  <div class="hero-shade"></div>
  <h1>NEED HELP PUBLISHING A BESTSELLER?</h1>
  <p>Lorem ipsum dolor sit amet, consectetur adipiscing elit. Proin pellentesque tellus eget elit tempus imperdiet. Donec tempor risus sed leo pellentesque vulputate.</p>
  <a class="btn-pill">Read More</a>
</section>

<section class="about">
  <div class="about-photo" role="img" aria-label="Photo of a person marking up a manuscript on a clipboard with a red pen"></div>
  <svg class="about-panel" width="1200" height="376" viewBox="0 0 1200 376" preserveAspectRatio="none"><polygon points="718,0 1200,0 1200,376 609,376" fill="#e1001a"/></svg>
  <div class="about-body">
    <h2>ABOUT <span>US</span></h2>
    <p>Lorem ipsum dolor sit amet, consectetur adipiscing elit. Proin pellentesque tellus eget elit tempus imperdiet. Donec tempor risus sed leo pellentesque vulputate. Nulla massa turpis, mattis nec tristique auctor, lacinia eget orci. Lorem ipsum dolor sit amet, consectetur adipiscing elit. Proin pellentesque tellus eget elit tempus imperdiet. Donec tempor risus sed leo pellentesque vulputate. Nulla massa turpis, mattis nec tristique auctor, lacinia eget orci.</p>
    <a class="btn-pill">Read More</a>
  </div>
</section>

<section class="services">
  <h2 class="section-title">OUR <span>SERVICES</span></h2>
  <p class="lead">We've carefully structured our packages to maximize value for every budget.</p>

  <div class="service" style="left:251px">
    <svg class="icon" viewBox="0 0 140 140"><circle cx="72" cy="72" r="66" fill="#444"/><circle cx="68" cy="68" r="66" fill="#e1001a"/>
      <g fill="none" stroke="#fff" stroke-width="3"><rect x="46" y="44" width="38" height="48" rx="3"/><rect x="56" y="38" width="18" height="10" rx="2"/><path d="M54 60h22M54 70h22M54 80h14"/><path d="M92 48v40l-4 6-4-6V48z"/></g></svg>
    <h3>WRITE</h3>
    <p>Lorem ipsum dolor sit amet, consectetur<br>adipiscing elit.</p>
  </div>
  <div class="service" style="left:593px">
    <svg class="icon" viewBox="0 0 140 140"><circle cx="72" cy="72" r="66" fill="#444"/><circle cx="68" cy="68" r="66" fill="#e1001a"/>
      <g fill="none" stroke="#fff" stroke-width="3"><path d="M48 40h30l12 12v44H48z"/><path d="M56 60h18M56 70h12"/><path d="M64 88l4-12 26-26 8 8-26 26z"/></g></svg>
    <h3>EDIT</h3>
    <p>Lorem ipsum dolor sit amet, consectetur<br>adipiscing elit.</p>
  </div>
  <div class="service" style="left:947px">
    <svg class="icon" viewBox="0 0 140 140"><circle cx="72" cy="72" r="66" fill="#444"/><circle cx="68" cy="68" r="66" fill="#e1001a"/>
      <g fill="none" stroke="#fff" stroke-width="3"><path d="M52 56V40h32v16"/><path d="M58 46h20M58 52h20"/><rect x="40" y="56" width="56" height="32" rx="5"/><path d="M48 66h40M48 74h40M56 82h24"/></g></svg>
    <h3>Typeset</h3>
    <p>Lorem ipsum dolor sit amet, consectetur<br>adipiscing elit.</p>
  </div>

  <a class="btn-pill">VIEW MORE SERVICES</a>
</section>

<section class="packages">
  <h2 class="section-title">SELECT <span>A PACKAGE</span></h2>

  <div class="plan plan-silver">
    <div class="plan-head">
      <svg viewBox="0 0 240 88" preserveAspectRatio="none"><path d="M0 0H240V70C200 94 160 56 120 72S40 92 0 70Z" fill="#474747"/></svg>
      <h3>SILVER</h3>
    </div>
    <div class="plan-price">$.02</div>
    <div class="plan-unit">(PER WORD)</div>
    <ul>
      <li><svg width="13" height="13" viewBox="0 0 14 14"><rect x="1" y="3" width="10" height="10" fill="none" stroke="#e1001a" stroke-width="1.6"/><path d="M3.5 7.5l2.5 2.5L13 2" fill="none" stroke="#e1001a" stroke-width="2"/></svg>Proofreading</li>
      <li><svg width="13" height="13" viewBox="0 0 14 14"><rect x="1" y="3" width="10" height="10" fill="none" stroke="#e1001a" stroke-width="1.6"/><path d="M3.5 7.5l2.5 2.5L13 2" fill="none" stroke="#e1001a" stroke-width="2"/></svg>Line Edit (Copy-editing)</li>
      <li><svg width="13" height="13" viewBox="0 0 14 14"><rect x="1" y="3" width="10" height="10" fill="none" stroke="#e1001a" stroke-width="1.6"/><path d="M3.5 7.5l2.5 2.5L13 2" fill="none" stroke="#e1001a" stroke-width="2"/></svg>Fix spelling and grammar</li>
      <li><svg width="13" height="13" viewBox="0 0 14 14"><rect x="1" y="3" width="10" height="10" fill="none" stroke="#e1001a" stroke-width="1.6"/><path d="M3.5 7.5l2.5 2.5L13 2" fill="none" stroke="#e1001a" stroke-width="2"/></svg>Sales copy/summary revision</li>
    </ul>
    <p class="plan-note">Lorem ipsum dolor<br>consectetur adipiscing</p>
    <a class="btn-pill">BEST ALL</a>
  </div>

  <div class="plan plan-gold">
    <div class="plan-head">
      <svg viewBox="0 0 265 105" preserveAspectRatio="none"><path d="M0 0H265V84C220 110 176 68 132 86S44 108 0 84Z" fill="#e1001a"/></svg>
      <h3>GOLD</h3>
    </div>
    <div class="plan-price">$.04</div>
    <div class="plan-unit">(PER WORD)</div>
    <ul>
      <li><svg width="13" height="13" viewBox="0 0 14 14"><rect x="1" y="3" width="10" height="10" fill="none" stroke="#e1001a" stroke-width="1.6"/><path d="M3.5 7.5l2.5 2.5L13 2" fill="none" stroke="#e1001a" stroke-width="2"/></svg>Proofreading</li>
      <li><svg width="13" height="13" viewBox="0 0 14 14"><rect x="1" y="3" width="10" height="10" fill="none" stroke="#e1001a" stroke-width="1.6"/><path d="M3.5 7.5l2.5 2.5L13 2" fill="none" stroke="#e1001a" stroke-width="2"/></svg>Line Edit (Copy-editing)</li>
      <li><svg width="13" height="13" viewBox="0 0 14 14"><rect x="1" y="3" width="10" height="10" fill="none" stroke="#e1001a" stroke-width="1.6"/><path d="M3.5 7.5l2.5 2.5L13 2" fill="none" stroke="#e1001a" stroke-width="2"/></svg>Fix spelling and grammar</li>
      <li><svg width="13" height="13" viewBox="0 0 14 14"><rect x="1" y="3" width="10" height="10" fill="none" stroke="#e1001a" stroke-width="1.6"/><path d="M3.5 7.5l2.5 2.5L13 2" fill="none" stroke="#e1001a" stroke-width="2"/></svg>Sales copy/summary revision</li>
      <li><svg width="13" height="13" viewBox="0 0 14 14"><rect x="1" y="3" width="10" height="10" fill="none" stroke="#e1001a" stroke-width="1.6"/><path d="M3.5 7.5l2.5 2.5L13 2" fill="none" stroke="#e1001a" stroke-width="2"/></svg>Organization and content</li>
      <li><svg width="13" height="13" viewBox="0 0 14 14"><rect x="1" y="3" width="10" height="10" fill="none" stroke="#e1001a" stroke-width="1.6"/><path d="M3.5 7.5l2.5 2.5L13 2" fill="none" stroke="#e1001a" stroke-width="2"/></svg>Plot and pacing</li>
      <li><svg width="13" height="13" viewBox="0 0 14 14"><rect x="1" y="3" width="10" height="10" fill="none" stroke="#e1001a" stroke-width="1.6"/><path d="M3.5 7.5l2.5 2.5L13 2" fill="none" stroke="#e1001a" stroke-width="2"/></svg>Manuscript Review</li>
    </ul>
    <a class="btn-pill">BEST ALL</a>
  </div>

  <div class="plan plan-platinum">
    <div class="plan-head">
      <svg viewBox="0 0 244 88" preserveAspectRatio="none"><path d="M0 0H244V70C204 94 162 56 122 72S40 92 0 70Z" fill="#474747"/></svg>
      <h3>PLATINUM</h3>
    </div>
    <div class="plan-price">$.06</div>
    <div class="plan-unit">(PER WORD)</div>
    <ul>
      <li><svg width="13" height="13" viewBox="0 0 14 14"><rect x="1" y="3" width="10" height="10" fill="none" stroke="#e1001a" stroke-width="1.6"/><path d="M3.5 7.5l2.5 2.5L13 2" fill="none" stroke="#e1001a" stroke-width="2"/></svg>Proofreading</li>
      <li><svg width="13" height="13" viewBox="0 0 14 14"><rect x="1" y="3" width="10" height="10" fill="none" stroke="#e1001a" stroke-width="1.6"/><path d="M3.5 7.5l2.5 2.5L13 2" fill="none" stroke="#e1001a" stroke-width="2"/></svg>Line Edit (Copy-editing)</li>
      <li><svg width="13" height="13" viewBox="0 0 14 14"><rect x="1" y="3" width="10" height="10" fill="none" stroke="#e1001a" stroke-width="1.6"/><path d="M3.5 7.5l2.5 2.5L13 2" fill="none" stroke="#e1001a" stroke-width="2"/></svg>Fix spelling and grammar</li>
      <li><svg width="13" height="13" viewBox="0 0 14 14"><rect x="1" y="3" width="10" height="10" fill="none" stroke="#e1001a" stroke-width="1.6"/><path d="M3.5 7.5l2.5 2.5L13 2" fill="none" stroke="#e1001a" stroke-width="2"/></svg>Sales copy/summary revision</li>
      <li><svg width="13" height="13" viewBox="0 0 14 14"><rect x="1" y="3" width="10" height="10" fill="none" stroke="#e1001a" stroke-width="1.6"/><path d="M3.5 7.5l2.5 2.5L13 2" fill="none" stroke="#e1001a" stroke-width="2"/></svg>Organization and content</li>
      <li><svg width="13" height="13" viewBox="0 0 14 14"><rect x="1" y="3" width="10" height="10" fill="none" stroke="#e1001a" stroke-width="1.6"/><path d="M3.5 7.5l2.5 2.5L13 2" fill="none" stroke="#e1001a" stroke-width="2"/></svg>Pre-publication proofread</li>
      <li><svg width="13" height="13" viewBox="0 0 14 14"><rect x="1" y="3" width="10" height="10" fill="none" stroke="#e1001a" stroke-width="1.6"/><path d="M3.5 7.5l2.5 2.5L13 2" fill="none" stroke="#e1001a" stroke-width="2"/></svg>Formatting (print and ebook)</li>
    </ul>
    <a class="btn-pill">BEST ALL</a>
  </div>
</section>

<section class="process">
  <h2 class="section-title">OUR <span>PROCESS</span></h2>
  <div class="process-steps">
    <svg class="connector" style="left:246px" width="90" height="16" viewBox="0 0 90 16"><path d="M0 8h78" stroke="#999" stroke-width="2" stroke-dasharray="6 5"/><path d="M78 2l10 6-10 6z" fill="#999"/></svg>
    <svg class="connector" style="left:460px" width="72" height="16" viewBox="0 0 72 16"><path d="M0 8h60" stroke="#999" stroke-width="2" stroke-dasharray="6 5"/><path d="M60 2l10 6-10 6z" fill="#999"/></svg>
    <svg class="connector" style="left:664px" width="72" height="16" viewBox="0 0 72 16"><path d="M0 8h60" stroke="#999" stroke-width="2" stroke-dasharray="6 5"/><path d="M60 2l10 6-10 6z" fill="#999"/></svg>
    <svg class="connector" style="left:866px" width="82" height="16" viewBox="0 0 82 16"><path d="M0 8h70" stroke="#999" stroke-width="2" stroke-dasharray="6 5"/><path d="M70 2l10 6-10 6z" fill="#999"/></svg>

    <div class="step" style="left:180px">
      <svg width="140" height="126" viewBox="0 0 140 126"><circle cx="60" cy="60" r="59" fill="#e1001a"/>
        <g fill="none" stroke="#fff" stroke-width="3"><path d="M42 80l4-14 28-28 10 10-28 28z"/><path d="M68 44l10 10"/></g>
        <circle cx="112" cy="102" r="16" fill="#3d3d3d" stroke="#fff" stroke-width="3"/><text x="112" y="108" fill="#fff" font-size="16" font-weight="700" text-anchor="middle" font-family="Roboto, sans-serif">1</text></svg>
      <p>Typos and grammatical errors.</p>
    </div>
    <div class="step" style="left:395px">
      <svg width="140" height="126" viewBox="0 0 140 126"><circle cx="60" cy="60" r="59" fill="#e1001a"/>
        <text x="60" y="56" fill="#fff" font-size="22" font-weight="700" text-anchor="middle" font-family="Roboto, sans-serif">ABC</text>
        <path d="M42 70l12 12 26-22" fill="none" stroke="#fff" stroke-width="4"/>
        <circle cx="112" cy="102" r="16" fill="#3d3d3d" stroke="#fff" stroke-width="3"/><text x="112" y="108" fill="#fff" font-size="16" font-weight="700" text-anchor="middle" font-family="Roboto, sans-serif">2</text></svg>
      <p>Spelling and word choice issues</p>
    </div>
    <div class="step" style="left:600px">
      <svg width="140" height="126" viewBox="0 0 140 126"><circle cx="60" cy="60" r="59" fill="#e1001a"/>
        <rect x="54" y="26" width="12" height="44" rx="3" fill="#fff"/><rect x="54" y="78" width="12" height="12" rx="2" fill="#fff"/>
        <circle cx="112" cy="102" r="16" fill="#3d3d3d" stroke="#fff" stroke-width="3"/><text x="112" y="108" fill="#fff" font-size="16" font-weight="700" text-anchor="middle" font-family="Roboto, sans-serif">3</text></svg>
      <p>Punctuation and style</p>
    </div>
    <div class="step" style="left:801px">
      <svg width="140" height="126" viewBox="0 0 140 126"><circle cx="60" cy="60" r="59" fill="#e1001a"/>
        <g fill="none" stroke="#fff" stroke-width="3"><path d="M42 32h26l12 12v46H42z"/><path d="M50 52h22M50 62h22M50 72h22M50 82h14"/></g>
        <circle cx="112" cy="102" r="16" fill="#3d3d3d" stroke="#fff" stroke-width="3"/><text x="112" y="108" fill="#fff" font-size="16" font-weight="700" text-anchor="middle" font-family="Roboto, sans-serif">4</text></svg>
      <p>Word choice, clarity and flow</p>
    </div>
    <div class="step" style="left:1013px">
      <svg width="140" height="126" viewBox="0 0 140 126"><circle cx="60" cy="60" r="59" fill="#e1001a"/>
        <g fill="none" stroke="#fff" stroke-width="3"><path d="M36 86L84 38v48z"/><path d="M70 62v14H56"/><path d="M42 44l12-12 12 12-12 12z"/></g>
        <circle cx="112" cy="102" r="16" fill="#3d3d3d" stroke="#fff" stroke-width="3"/><text x="112" y="108" fill="#fff" font-size="16" font-weight="700" text-anchor="middle" font-family="Roboto, sans-serif">5</text></svg>
      <p>Sentence structure and craft</p>
    </div>
  </div>
</section>

<section class="testimonials">
  <div class="testimonials-photo" role="img" aria-label="Dimmed photo of two people smiling in front of a sketched background"></div>
  <h2 class="section-title">TESTIMONIALS</h2>
  <div class="quote" style="left:365px">
    <blockquote>" Quisque in laoreet ipsum, vel dapibus est. Nulla pellentesque faucibus vulputate. Integer consequat leo eget dui interdum vulputate. Sed commodo sagittis lorem nec rutrum. Nam at tortor imperdiet,</blockquote>
    <div class="avatar" role="img" aria-label="Client portrait"></div>
    <div class="name">-&nbsp; Person Name</div>
    <div class="city">-&nbsp; City Name</div>
  </div>
  <div class="quote" style="left:851px">
    <blockquote>" Quisque in laoreet ipsum, vel dapibus est. Nulla pellentesque faucibus vulputate. Integer consequat leo eget dui interdum vulputate. Sed commodo sagittis lorem nec rutrum. Nam at tortor imperdiet,</blockquote>
    <div class="avatar" role="img" aria-label="Client portrait"></div>
    <div class="name">-&nbsp; Person Name</div>
    <div class="city">-&nbsp; City Name</div>
  </div>
</section>

<footer class="site-footer">
  <div class="footer-col footer-brand">
    <div class="name">Birch And Harbor</div>
    <p>At vero eos et accusamus et iusto odio dignissimos ducimus qui blanditiis</p>
    <div class="footer-social"><span></span><span></span><span></span><span></span></div>
  </div>
  <div class="footer-col newsletter">
    <h4>Signup For Newsletter</h4>
    <p>On the other hand, we denounce with righteous indignation and dislike men who are so beguiled</p>
    <div class="field">Enter Your Email</div>
    <div class="btn-sub">SUBSCRIBE</div>
  </div>
  <div class="footer-col contact">
    <h4>Contact Us</h4>
    <ul>
      <li><svg width="12" height="14" viewBox="0 0 12 16"><path d="M6 0a6 6 0 0 0-6 6c0 4.5 6 10 6 10s6-5.5 6-10a6 6 0 0 0-6-6zm0 8.5A2.5 2.5 0 1 1 6 3.5a2.5 2.5 0 0 1 0 5z" fill="#fff"/></svg><span>48 Quill Lane, Fairview,<br>CA 90000 USA.</span></li>
      <li><svg width="13" height="13" viewBox="0 0 24 24"><path fill="#fff" d="M6.6 10.8a15.1 15.1 0 0 0 6.6 6.6l2.2-2.2a1 1 0 0 1 1-.25 11.4 11.4 0 0 0 3.6.6 1 1 0 0 1 1 1V20a1 1 0 0 1-1 1A17 17 0 0 1 3 4a1 1 0 0 1 1-1h3.5a1 1 0 0 1 1 1c0 1.25.2 2.45.6 3.6a1 1 0 0 1-.25 1z"/></svg><span>1-800-555-0199</span></li>
      <li><svg width="14" height="12" viewBox="0 0 16 12"><path d="M0 0h16v12H0z" fill="#fff"/><path d="M0 0l8 6 8-6" fill="none" stroke="#000" stroke-width="1.4"/></svg><span>contact@birchandharbor.com</span></li>
    </ul>
  </div>
  <div class="footer-col quick-links">
    <h4>Quick Links</h4>
    <ul>
      <li>Home</li><li>About</li><li>Process</li><li>Pricing</li><li>Contact Us</li>
    </ul>
  </div>
  <div class="footer-rule"></div>
  <p class="copyright">Copyrights © 2018. Allrights Reserved.</p>
</footer>

</body>
</html>
```